Business card design for a dynamic IT consulting company

We need a business card design for a young firm, specialized in the Telecommunications/Consulting industry. The name of the company is Quindor and Partners Business Consulting Ltd. (Short name: Quindor and Partnes)
Quindor = solve read reverse, so we aim to be uncomplicated and solution-oriented. The small pipe in our logo is also related to the word solve. So we need a new business card design, which is simple, eye catching and something non traditional (I would probably prefer a square shaped design rather than a rectangle, but open for suggestions). Attached our logo.

Target Market(s)

Usually our customers are Tier1 Telecoms providers (Q-Netra, Palorix, etc) and their executives.

Industry/Entity Type

Business

Contact Information for Business Card

Name: Bence Tolnavari
Email: b.tolnavari@quindor.hu
Web: www.quindor.hu
Mobile: +36 30 518 2769
Title: Managing Director

Optional:
Company name: Quindor and Partners Ltd.
Address: 1087 Budapest, Tolvenka str. 28/C, Hungary

Font styles to use
Other font styles liked:
• helveticaneue_medium, Prime Regular are used now.

Colors

Designer to choose colors to be used in the design.

Requirements
Must have
• I would like to have a 2 sided design.
Nice to have
• I thought if we make the logo a bit bigger (without the company name), that could go to the back with the company name below. I though, if the pipe in the logo is somehow touchable on the business card, would be nice and unique.

```html
<!DOCTYPE html>
<html lang="en">
<head>
<meta charset="utf-8">
<title>Quindor and Partners – Business Card</title>
<link href="https://fonts.googleapis.com/css2?family=Source+Sans+3:wght@400;700&display=swap" rel="stylesheet">
<style>
  :root {
    --canvas: #e9e6e1;
    --card-black: #0d0d0f;
    --text-white: #f4f4f4;
    --brand-cyan: #29aae1;
    --brand-magenta: #b62d8e;
    --shadow: rgba(0, 0, 0, 0.28);
  }
  * { box-sizing: border-box; margin: 0; padding: 0; }
  html, body {
    width: 1200px;
    height: 900px;
    overflow: hidden;
    background: var(--canvas);
    font-family: "Source Sans 3", "Helvetica Neue", Arial, sans-serif;
  }
  .stage {
    position: relative;
    width: 1200px;
    height: 900px;
  }
  .card {
    position: absolute;
    width: 520px;
    height: 300px;
    background: var(--card-black);
    box-shadow: 0 10px 30px var(--shadow);
    overflow: hidden;
  }

  /* Front face */
  .card--front { left: 90px; top: 130px; }
  .brand {
    position: absolute;
    left: 0; right: 0; top: 0; bottom: 0;
    display: flex;
    align-items: center;
    justify-content: center;
    gap: 16px;
  }
  .brand__square {
    width: 22px; height: 22px;
    background: var(--brand-cyan);
  }
  .brand__name {
    color: var(--text-white);
    font-weight: 400;
    font-size: 36px;
    line-height: 1;
  }

  /* Back face */
  .card--back { left: 590px; top: 470px; }
  .card__waves { position: absolute; inset: 0; }
  .contact {
    position: absolute;
    left: 40px; top: 30px;
    color: var(--text-white);
  }
  .contact__name {
    color: var(--brand-cyan);
    font-size: 21px;
    font-weight: 700;
    line-height: 1.2;
  }
  .contact__title {
    margin-left: 8px;
    font-size: 14px;
  }
  .contact__list {
    list-style: none;
    margin-top: 18px;
    margin-left: 4px;
    font-size: 16px;
    line-height: 21px;
  }
  .contact__list li { display: flex; align-items: center; gap: 10px; }
  .contact__list svg { width: 11px; height: 11px; flex: none; }
  .address {
    position: absolute;
    left: 44px; top: 184px;
    color: var(--text-white);
    font-size: 15px;
    line-height: 19px;
    font-style: normal;
  }
  .card__marker {
    position: absolute;
    right: 70px; top: 40px;
    width: 18px; height: 18px;
    background: var(--brand-cyan);
  }
  .card__web {
    position: absolute;
    right: 40px; top: 180px;
    color: var(--text-white);
    font-size: 14px;
  }
</style>
</head>
<body>
<main class="stage">

  <section class="card card--front" aria-label="Card front">
    <div class="brand">
      <span class="brand__square"></span>
      <span class="brand__name">Quindor and Partners</span>
    </div>
  </section>

  <section class="card card--back" aria-label="Card back">
    <svg class="card__waves" viewBox="0 0 520 300" preserveAspectRatio="none" aria-hidden="true">
      <path d="M0,290 C140,300 290,262 360,192 C410,145 460,128 520,122 L520,300 L0,300 Z" fill="var(--brand-cyan)"/>
      <path d="M0,262 C150,272 290,235 390,165 C300,245 150,282 0,282 Z" fill="var(--brand-magenta)"/>
      <path d="M0,282 C150,282 300,245 390,165" fill="none" stroke="var(--card-black)" stroke-width="4"/>
    </svg>

    <div class="contact">
      <h1 class="contact__name">Bence Tolnavari</h1>
      <p class="contact__title">Managing Director</p>
      <ul class="contact__list">
        <li>
          <svg viewBox="0 0 12 12"><path d="M1,8 C1,5 3,3 6,3 C9,3 11,5 11,8 L8,8 L8,6.5 L4,6.5 L4,8 Z M3,9 L9,9 L9,11 L3,11 Z" fill="var(--brand-cyan)"/></svg>
          <span>+36 30 518 2769</span>
        </li>
        <li>
          <svg viewBox="0 0 12 12"><rect x="1" y="3" width="10" height="7" fill="var(--brand-cyan)"/><path d="M1,3 L6,7 L11,3" fill="none" stroke="var(--card-black)" stroke-width="1"/></svg>
          <span>b.tolnavari@quindor.hu</span>
        </li>
        <li>
          <svg viewBox="0 0 12 12"><circle cx="6" cy="6" r="5" fill="var(--brand-cyan)"/><path d="M4,3 L6,5 L5,7 L7,9" fill="none" stroke="var(--card-black)" stroke-width="1"/></svg>
          <span>www.quindor.hu</span>
        </li>
      </ul>
    </div>

    <address class="address">
      Quindor and Partners Ltd.<br>
      1087 Budapest, Tolvenka str.<br>
      28/C, Hungary
    </address>

    <span class="card__marker"></span>
    <span class="card__web">www.quindor.hu</span>
  </section>

</main>
</body>
</html>
```